Calloway needs a modernized design

We would like a modern update (that can be responsive) to our existing website. Attached are the two existing pages we would like new concepts of - our home page and a page about one of our locations.

Calloway is provides executive offices and virtual office services. Startups, law firms, and financial services are our primary clients. We would like a professional, clean design, leaning towards minimalist. We intend to greatly reduce/eliminate the long paragraphs of text.

Requirements
Must have
• A design that can be responsive
Nice to have
• Large image(s) on home page that rotate.

```html
<!DOCTYPE html>
<html lang="en">
<head>
<meta charset="utf-8">
<title>Calloway Business Centers</title>
<link href="https://fonts.googleapis.com/css2?family=Lato:wght@400;700&family=Oswald:wght@400;500&family=Roboto+Condensed:wght@400;700&display=swap" rel="stylesheet">
<style>
:root{
  --navy:#2a3b6b;
  --red:#d4472f;
  --light:#e4e9ed;
  --tile:#e9ecef;
  --field:#e8ebee;
  --text:#333;
  --muted:#666;
  --white:#fff;
}
*{box-sizing:border-box;margin:0;padding:0}
html,body{width:819px;height:1200px;overflow:hidden;background:var(--white)}
body{position:relative;font-family:"Lato",sans-serif;color:var(--text)}
.abs{position:absolute}
.header{left:0;top:0;width:819px;height:62px;border-bottom:1px solid #e2e2e2}
.brand{left:50px;top:12px;display:flex;align-items:center;gap:6px}
.brand-dot{width:38px;height:38px;border-radius:50%;background:var(--navy)}
.brand-name{font-family:"Lato",sans-serif;font-size:17px;font-weight:700;color:var(--navy);line-height:1}
.brand-name small{display:block;font-size:7.5px;letter-spacing:.5px;margin-top:2px;font-weight:700}
.phone{top:19px;font-size:9px;color:#222;line-height:1.3}
.phone b{display:block;font-size:11.5px;font-weight:400;color:var(--navy)}
.phone-divider{left:509px;top:20px;width:1px;height:26px;background:#ddd}
.social{display:flex;gap:4px}
.social span{width:27px;height:27px;border-radius:50%;border:2px solid var(--red)}
.social span:nth-child(1){border-color:#35b3e6}
.social span:nth-child(3){border-color:#1a6aa8}
.nav{left:0;top:62px;width:819px;height:26px;display:flex;gap:30px;padding-left:68px;align-items:center;font-size:9.5px;color:#222}
.hero{left:0;top:88px;width:819px;height:321px;background:linear-gradient(100deg,#d9dde2 0%,#b7bfc9 35%,#5d6f8c 60%,#aab4c2 100%)}
.hero-title{left:286px;top:247px;width:459px;height:40px;background:var(--navy);color:var(--white);font-family:"Oswald",sans-serif;font-weight:500;font-size:29px;padding-left:11px;line-height:40px;clip-path:polygon(0 0,95% 0,100% 100%,0 100%)}
.hero-sub{left:358px;top:287px;width:409px;height:26px;background:var(--red);color:var(--white);font-family:"Roboto Condensed",sans-serif;font-size:18px;line-height:26px;text-align:right;padding-right:12px;clip-path:polygon(3% 0,100% 0,100% 100%,0 100%)}
.dots{left:50px;top:382px;display:flex;gap:3px}
.dots i{width:8px;height:8px;border-radius:50%;background:var(--white)}
.dots i:first-child{background:var(--navy);border:1px solid var(--white)}
.services{left:0;top:409px;width:819px;height:88px;background:var(--navy)}
.tile{top:13px;width:134px;height:63px;background:var(--tile);display:flex;align-items:center;justify-content:center;text-align:center;font-family:"Roboto Condensed",sans-serif;font-size:12.5px;color:var(--navy);line-height:1.05;text-transform:uppercase}
.main{left:0;top:497px;width:819px;height:479px;background:var(--light)}
.intro{left:50px;top:525px;width:460px;font-size:12.2px;font-weight:700;color:#222;line-height:1.35}
.card{left:75px;width:448px;height:114px;background:var(--white);border-radius:16px;padding:16px 20px 0 42px}
.card h2{font-family:"Roboto Condensed",sans-serif;font-weight:700;font-size:17px;color:var(--navy);margin-bottom:6px}
.card p{font-size:9.6px;color:#555;line-height:1.85}
.more{display:inline-block;width:9px;height:9px;border-radius:50%;background:var(--red);vertical-align:-1px}
.badge-icon{width:50px;height:50px;border-radius:50%;background:var(--navy);border:2px solid var(--navy);overflow:hidden}
.badge-icon::after{content:"";display:block;width:25px;height:50px;margin-left:23px;background:var(--white)}
.form{left:542px;top:526px;width:227px;height:419px;background:var(--white)}
.form-head{height:59px;background:var(--red);color:var(--white);font-family:"Roboto Condensed",sans-serif;font-weight:700;font-size:17px;text-align:center;padding-top:17px;clip-path:polygon(0 0,100% 0,100% 80%,50% 100%,0 80%)}
.field{position:absolute;left:19px;width:189px}
.field label{display:block;font-size:8px;color:var(--muted);margin-bottom:3px}
.field div{height:24px;background:var(--field);font-size:8.5px;color:#333;padding:8px 6px 0;position:relative}
.caret{position:absolute;right:9px;top:9px;border:4px solid transparent;border-top:5px solid #555}
.submit{position:absolute;left:19px;top:382px;width:189px;height:24px;background:var(--navy);color:var(--white);font-family:"Roboto Condensed",sans-serif;font-weight:700;font-size:11px;text-align:center;line-height:24px}
.footer{left:0;top:976px;width:819px;height:177px;background:var(--navy);color:var(--white)}
.footer h3{position:absolute;top:18px;font-size:10px;font-weight:700}
.links{position:absolute;left:50px;top:38px;font-size:8.8px;line-height:15.2px;color:#dfe4ee}
.contact{position:absolute;left:174px;top:38px;font-size:8.8px;line-height:13px;color:#dfe4ee}
.photo{position:absolute;left:358px;top:40px;width:227px;height:120px;background:linear-gradient(180deg,#9fb6cf 0%,#8c7d6e 45%,#5e7a43 75%,#4d6637 100%)}
.seal-box{position:absolute;left:604px;top:40px;width:165px;height:120px;background:var(--white);display:flex;align-items:center;justify-content:center}
.seal{width:92px;height:92px;border-radius:50%;background:var(--navy);border:5px solid #b6bcc8}
.bottom{left:50px;top:1164px;font-size:8.8px;color:#444;line-height:14px}
</style>
</head>
<body>
<header class="abs header">
  <div class="abs brand"><span class="brand-dot"></span><span class="brand-name">CALLOWAY<small>BUSINESS CENTERS</small></span></div>
  <div class="abs phone" style="left:427px">Dallas<b>214.555.0142</b></div>
  <div class="abs phone-divider"></div>
  <div class="abs phone" style="left:522px">Houston<b>713.555.0187</b></div>
  <div class="abs social" style="left:618px;top:17px" aria-label="Social links"><span></span><span></span><span></span><span></span><span></span></div>
</header>
<nav class="abs nav"><span>HOME</span><span>PROPERTIES</span><span>VIRTUAL TOURS &amp; VIDEOS</span><span>PHOTOS</span><span>BROKER REFERRALS</span></nav>

<section class="abs hero" role="img" aria-label="Colleagues gathered around a meeting table reviewing documents"></section>
<div class="abs hero-title">ON DEMAND MEETING ROOMS</div>
<div class="abs hero-sub">THAT FIT YOUR NEEDS AND YOUR BUDGET</div>
<div class="abs dots"><i></i><i></i><i></i><i></i><i></i></div>

<section class="abs services">
  <div class="abs tile" style="left:54px">Executive Office<br>Suites</div>
  <div class="abs tile" style="left:200px">On-Demand<br>Meeting Rooms</div>
  <div class="abs tile" style="left:345px">On-Demand<br>Training Rooms</div>
  <div class="abs tile" style="left:490px">Virtual Office<br>Solutions</div>
  <div class="abs tile" style="left:635px">Video Conference<br>Solutions</div>
</section>

<main class="abs main"></main>
<p class="abs intro">Come See Why Smarter Companies are Choosing Calloway Business Centers' Dallas, Ft. Worth and Houston Executive Office Suites, Virtual Offices, Meeting Rooms and Video Conferencing.</p>

<article class="abs card" style="top:588px"><h2>OUR VALUE</h2><p>Either you need Dallas/Ft. Worth Office Space, Dallas Executive Suites, Ft. Worth Executive Suites, Houston Office Space, Houston Executive Suites, or maybe you simply need a place to stop in and use an on-demand office or meeting room... <span class="more"></span></p></article>
<article class="abs card" style="top:709px"><h2>OUR COMMUNITY</h2><p>Companies that partner with Calloway share more than a prestigious address. They also share ideas and services. Our Executive Office Business Centers are places where savvy, growing companies can network, interact and learn from one another... <span class="more"></span></p></article>
<article class="abs card" style="top:830px"><h2>OUR SERVICE</h2><p>Calloway Business Centers positions its management team in every one of its business centers - we operate with an open-door policy as a medium-sized company without all of the corporate bureaucracy and red tape... <span class="more"></span></p></article>
<div class="abs badge-icon" style="left:50px;top:620px"></div>
<div class="abs badge-icon" style="left:50px;top:741px"></div>
<div class="abs badge-icon" style="left:56px;top:863px"></div>

<form class="abs form">
  <div class="form-head">REQUEST INFORMATION</div>
  <div class="field" style="top:70px"><label>Full Name</label><div></div></div>
  <div class="field" style="top:113px"><label>Last Name</label><div></div></div>
  <div class="field" style="top:157px"><label>Company Name</label><div></div></div>
  <div class="field" style="top:200px"><label>Phone Number</label><div></div></div>
  <div class="field" style="top:244px"><label>Email Address</label><div></div></div>
  <div class="field" style="top:287px"><label>Property Interested In</label><div><span class="caret"></span></div></div>
  <div class="field" style="top:331px"><label>Product Interested In</label><div>Executive Offices<span class="caret"></span></div></div>
  <div class="submit">SUBMIT</div>
</form>

<footer class="abs footer">
  <h3 style="left:50px">Quick Links</h3>
  <div class="links">Home<br>Properties<br>Virtual Tours &amp; Videos<br>Photos<br>Broker Referrals<br>About Us<br>Contact Us</div>
  <h3 style="left:174px">Contact Info</h3>
  <div class="contact">228, Lorem Ipsum dolor sit,<br>dosis amet 858485<br><br>Dallas 214.555.0142<br>Houston 713.555.0187<br><br>Website:<br>www.callowayoffices.example/</div>
  <h3 style="left:358px">View Current Specials</h3>
  <div class="photo" role="img" aria-label="Brick office building with trees and parked cars"></div>
  <div class="seal-box"><div class="seal" role="img" aria-label="Anniversary seal"></div></div>
</footer>

<div class="abs bottom">Forums | Testimonials | Careers | FAQs | Furniture | Specials | Terms of Use | Privacy Policy | Sitemap<br>Copyright © 2016 Calloway Business Centers. All Rights Reserved</div>
<div class="abs social" style="left:620px;top:1164px" aria-label="Social links"><span></span><span></span><span></span><span></span><span></span></div>
</body>
</html>
```